Finiding oppertunites in Real Estate 6.15.20

size of ad 7” x 9.6”
1-I like the ad to stand out and attract people's attention.
2-you should be able to see the text of the ad clearly .. see the attachment anything in yellow is instructions.
3-the list of topics should not be the main part of the ad
4-if you decide you want a picture or vector of a person .. (you decide)
then it should be a white male about 25-30 years old wearing a solid white or blue shirt and not long hair.
5-leave 1 inch for footer
see attachment
Good luck

Target Market(s)

potential male students 25-35 years of age

Industry/Entity Type

Education

Requirements
Must have
• will stand out and people would want to see it.
should be able to read the words of ad
Nice to have
• how to make money in real estate on one line

```html
<!DOCTYPE html>
<html lang="en">
<head>
<meta charset="utf-8">
<title>Real Estate Career Course</title>
<link rel="stylesheet" href="https://fonts.googleapis.com/css2?family=Barlow+Condensed:wght@400;500;600;700;800&family=Barlow+Semi+Condensed:wght@700&family=Poppins:wght@600&display=swap">
<style>
  :root{
    --stage:#e6e6e8;
    --paper:#ededee;
    --paper-grey:#d5d6d9;
    --navy:#0d2250;
    --blue:#1e4a86;
    --ink:#132a55;
    --accent:#2a5aa0;
    --footer-grey:#c9cacd;
    --white:#ffffff;
  }
  *{margin:0;padding:0;box-sizing:border-box}
  html,body{width:1200px;height:1200px;overflow:hidden;background:var(--stage)}
  .flyer{position:absolute;left:190px;top:20px;width:820px;height:1160px;background:var(--paper);overflow:hidden;font-family:"Barlow Condensed",sans-serif;color:var(--ink);box-shadow:0 6px 24px rgba(0,0,0,.18)}
  .backdrop{position:absolute;inset:0}
  .abs{position:absolute}
  .title{left:440px;top:38px;width:360px;text-align:center;font-weight:700;font-size:50px;line-height:.96;color:var(--ink);letter-spacing:-.3px}
  .promise-list{left:50px;top:132px;width:400px;list-style:none;color:var(--white)}
  .promise-list li{display:flex;gap:12px;font-size:30px;font-weight:500;line-height:1.14;padding:10px 0 14px;border-bottom:2px solid rgba(255,255,255,.85)}
  .promise-list li:first-child span{white-space:nowrap}
  .promise-list li:last-child{border-bottom:none}
  .promise-list svg{flex:none;width:22px;height:22px;margin-top:6px}
  .portrait-frame{left:490px;top:188px;width:330px;height:590px;clip-path:polygon(0 0,100% 0,100% 100%,83% 100%,0 71%)}
  .portrait{width:100%;height:100%;border-radius:150px 150px 0 0;background:linear-gradient(180deg,#b9a595 0%,#d9c6b6 28%,#e9e9ea 44%,#2f5797 60%,#1e3f78 100%)}
  .screen-art{left:110px;top:494px;width:290px;height:150px;border-radius:6px;border:6px solid var(--navy);background:linear-gradient(135deg,#f2a228 0%,#e98a1d 60%,#c8761c 100%)}
  .laptop-base{left:94px;top:653px;width:322px;height:16px;border-radius:0 0 10px 10px;background:var(--navy)}
  .remote{left:50px;top:704px;font-weight:800;font-size:64px;line-height:.86;color:var(--ink)}
  .divider{left:296px;top:714px;width:3px;height:106px;background:var(--ink)}
  .count{left:314px;top:688px;font-family:"Poppins",sans-serif;font-weight:600;font-size:104px;line-height:1;color:var(--ink);letter-spacing:-4px}
  .session{left:439px;top:700px;font-family:"Barlow Semi Condensed",sans-serif;font-weight:700;font-size:46px;line-height:.9;color:var(--ink)}
  .start{left:320px;top:788px;font-size:31px;font-weight:400;color:var(--ink)}
  .start span{color:var(--accent)}
  .topics-tag{left:50px;top:905px;width:180px;height:80px}
  .topics-tag p{position:absolute;left:0;top:10px;width:160px;text-align:center;font-size:27px;font-weight:500;line-height:1.1;color:var(--ink)}
  .topics{left:252px;top:866px;display:grid;grid-template-columns:198px 198px 190px;row-gap:8px;list-style:none}
  .topics li{display:flex;align-items:center;gap:9px;font-size:17px;color:var(--ink);height:25px}
  .topics svg{width:19px;height:19px;flex:none}
  .contact-title{left:126px;top:1074px;color:var(--white);font-size:26px;font-weight:400;line-height:1}
  .contact-phone{left:126px;top:1100px;color:var(--white);font-size:33px;font-weight:700;line-height:1}
  .details{font-size:19px;color:var(--ink);display:flex;align-items:center;gap:8px;white-space:nowrap}
  .details svg{width:15px;height:15px}
</style>
</head>
<body>
<svg width="0" height="0" style="position:absolute">
  <defs>
    <symbol id="tick-box" viewBox="0 0 24 24">
      <path d="M19 12v8H4V5h11" fill="none" stroke="currentColor" stroke-width="2" stroke-linejoin="round"/>
      <path d="M8 11l4 4 9-10" fill="none" stroke="currentColor" stroke-width="2" stroke-linecap="round" stroke-linejoin="round"/>
    </symbol>
  </defs>
</svg>

<main class="flyer">
  <svg class="backdrop" viewBox="0 0 820 1160" width="820" height="1160">
    <rect width="820" height="1160" fill="var(--paper-grey)"/>
    <polygon points="250,0 820,0 820,108 640,192 520,174" fill="var(--paper)"/>
    <path d="M0 0 H250 L510 168 Q520 176 520 190 V282 Q520 292 510 298 L236 474 Q222 483 208 492 L0 655 Z" fill="var(--navy)"/>
    <path d="M0 0 H250 L510 168 Q518 174 518 186 V276 Q518 286 510 294 L440 372 Q430 382 430 396 V404 Q430 414 420 420 L236 472 Q220 480 204 472 L0 355 Z" fill="var(--blue)"/>
    <polygon points="0,655 412,562 820,800 820,1160 0,1160" fill="var(--paper)"/>
    <rect x="0" y="1043" width="820" height="117" fill="var(--footer-grey)"/>
    <path d="M0 1053 H284 Q298 1053 308 1062 L418 1160 H0 Z" fill="var(--navy)"/>
    <g transform="translate(82 1103)" fill="none" stroke="var(--white)" stroke-width="2">
      <polygon points="0,-29 25,-14.5 25,14.5 0,29 -25,14.5 -25,-14.5"/>
      <path d="M-4 -11 q-6 0 -6 11 t6 11 l4 -3 -3 -5 -3 1 q-1 -4 0 -8 l3 1 3 -5 z" stroke-linejoin="round"/>
    </g>
    <polygon points="52,905 210,905 228,944 210,984 52,984" fill="none" stroke="var(--ink)" stroke-width="2"/>
  </svg>

  <h1 class="abs title">REAL ESTATE<br>CAREER COURSE</h1>

  <ul class="abs promise-list">
    <li><svg><use href="#tick-box"/></svg><span>How to Make Money In Real Estate?</span></li>
    <li><svg><use href="#tick-box"/></svg><span>For those who have started or<br>would like to go into Real Estate.</span></li>
    <li><svg><use href="#tick-box"/></svg><span>An investment in knowledge<br>opens up untold opportunities.</span></li>
  </ul>

  <div class="abs portrait-frame">
    <div class="portrait" role="img" aria-label="Photo of a smiling young man in a blue suit, white shirt and dark tie"></div>
  </div>
  <div class="abs screen-art" role="img" aria-label="Illustration of a laptop showing an online real estate lecture, with a student sitting on its edge"></div>
  <div class="abs laptop-base"></div>

  <h2 class="abs remote">REMOTE<br>SESSIONS</h2>
  <div class="abs divider"></div>
  <div class="abs count">12</div>
  <div class="abs session">session<br>course</div>
  <p class="abs start">Classes starting <span>June 16</span></p>

  <div class="abs topics-tag"><p>A partial listing of Topics</p></div>

  <ul class="abs topics">
    <li><svg><use href="#tick-box"/></svg>Single-family</li>
    <li><svg><use href="#tick-box"/></svg>Investment properties</li>
    <li><svg><use href="#tick-box"/></svg>Development</li>
    <li><svg><use href="#tick-box"/></svg>Multifamily</li>
    <li><svg><use href="#tick-box"/></svg>Foreclosures</li>
    <li><svg><use href="#tick-box"/></svg>Financial modeling</li>
    <li><svg><use href="#tick-box"/></svg>Management</li>
    <li><svg><use href="#tick-box"/></svg>Rehab</li>
    <li><svg><use href="#tick-box"/></svg>HUD properties</li>
    <li><svg><use href="#tick-box"/></svg>Real Estate Concepts</li>
    <li><svg><use href="#tick-box"/></svg>Foreclosures</li>
    <li><svg><use href="#tick-box"/></svg>Due Diligence</li>
    <li><svg><use href="#tick-box"/></svg>Real Estate law</li>
    <li><svg><use href="#tick-box"/></svg>Short sales</li>
  </ul>

  <p class="abs contact-title">Contact Us Today</p>
  <p class="abs contact-phone">00198765432</p>

  <p class="abs details" style="left:426px;top:1076px">
    <svg viewBox="0 0 16 16"><path d="M2 6q6-5 12 0l-2 2-2-1V5H6v2L4 8z M4 9h8l1 5H3z" fill="var(--ink)"/></svg>000 . 5550 . 1942
  </p>
  <p class="abs details" style="left:596px;top:1076px">
    <svg viewBox="0 0 16 16"><rect x="1" y="3" width="14" height="10" fill="var(--ink)"/><path d="M1 3l7 6 7-6" fill="none" stroke="#fff" stroke-width="1.3"/></svg>hello@fairviewcourse.com
  </p>
  <p class="abs details" style="left:426px;top:1105px">
    <svg viewBox="0 0 16 16"><path d="M8 1a5 5 0 0 1 5 5c0 4-5 9-5 9S3 10 3 6a5 5 0 0 1 5-5z" fill="var(--ink)"/><circle cx="8" cy="6" r="2" fill="#fff"/></svg>27 Harbor Lane Fairview, WI 54000
  </p>
</main>
</body>
</html>
```